Beautiful design for wordpress

I need a beautiful, colourful and feminine website. My business is called 'The Velvet Lantern', and I sell crystals, books, CD's, pendulums and other metaphysical items. I also provide Reiki (energy healing).
I want this design to be eye catching and inspire happiness and joy in those who see it. And I would love to see the use of the logo and its colours :)
Please add these on the web design: Home, About, Online store, Blog

Industry/Entity Type

Business

Requirements
Must have
• Colourful and playful, must use the logo somewhere, have the words on a menu saying 'Home, Blog, Online store and about' (or similar to those)And the design must stand out!
Should not have
• grey, brown and other boring colours.

```html
<!DOCTYPE html>
<html lang="en">
<head>
<meta charset="utf-8">
<title>The Velvet Lantern — Crystals &amp; Gifts</title>
<link href="https://fonts.googleapis.com/css2?family=Lobster&family=Open+Sans:wght@400;600&display=swap" rel="stylesheet">
<style>
:root{
  --orange:#f7931e;
  --coral:#f26a6a;
  --coral-dark:#ee5a5f;
  --peach:#fde3c8;
  --cream:#fdf7f1;
  --ink:#555;
  --ink-soft:#888;
  --line:#ececec;
  --dark:#4a4a4a;
  --white:#fff;
}
*{box-sizing:border-box;margin:0;padding:0}
html,body{width:835px;height:1200px;overflow:hidden;background:var(--white)}
body{position:relative;font-family:"Open Sans",Arial,sans-serif;color:var(--ink)}
.abs{position:absolute}
.script{font-family:"Lobster",cursive}

/* header */
.site-header{left:0;top:0;width:835px;height:58px;background:var(--white);z-index:3}
.brand{left:92px;top:0;width:108px;height:108px;border-radius:50%;background:var(--white);z-index:4;display:flex;align-items:center;justify-content:center;text-align:center;flex-direction:column}
.brand-name{font-family:"Lobster",cursive;font-size:17px;line-height:18px;color:var(--coral-dark);width:80px}
.nav{right:68px;top:21px;display:flex;gap:18px;z-index:4}
.nav a{font-family:"Lobster",cursive;font-size:15px;color:#666;text-decoration:none}
.nav a.current{color:var(--orange)}

/* hero */
.hero{left:0;top:58px;width:835px;height:364px;background:linear-gradient(90deg,#f8b56f 0%,#fbd3a8 35%,#f3c09a 60%,#7a4a36 100%)}
.hero-photo{left:330px;top:58px;width:505px;height:364px;background:radial-gradient(ellipse at 55% 45%,#e9b596 0%,#b27256 40%,rgba(110,60,40,.0) 75%)}
.hero-title{left:91px;top:155px;font-size:38px;color:var(--coral-dark)}
.hero-text{left:91px;top:222px;width:340px;font-family:"Lobster",cursive;font-size:18px;line-height:28px;color:var(--white);font-style:normal}
.hero-btn{left:91px;top:302px;width:103px;height:30px;border-radius:6px;background:var(--coral);color:var(--white);font-family:"Lobster",cursive;font-size:19px;display:flex;align-items:center;justify-content:center}
.hero-arrow{top:220px}

/* promo strip */
.promos{left:0;top:422px;width:835px;height:146px;background:var(--cream);border-bottom:1px solid var(--line)}
.promo{top:438px;width:204px;height:107px;border-radius:3px;overflow:hidden}
.promo-label{left:10px;top:22px;font-size:19px;line-height:23px}
.promo-rule{left:10px;top:76px;width:70px;height:1px}
.promo-link{left:12px;top:85px;font-size:9px;font-weight:600}

/* sidebar */
.section-title{font-family:"Lobster",cursive;font-size:16px;color:var(--orange)}
.cat-list{left:91px;top:617px;width:175px;list-style:none;border-top:1px solid var(--line)}
.cat-list li{height:28px;display:flex;align-items:center;padding-left:21px;font-size:11px;color:#444;background:linear-gradient(#fff,#f6f6f6);border-bottom:1px solid #fff;position:relative}
.cat-list li::before{content:"";position:absolute;left:10px;top:11px;border-left:4px solid var(--orange);border-top:3px solid transparent;border-bottom:3px solid transparent}
.newsletter{left:91px;top:828px;width:175px;height:125px;border:2px solid #f1f1f1;background:var(--white)}
.newsletter h3{position:absolute;left:5px;top:8px;font-family:"Lobster",cursive;font-weight:400;font-size:13px;color:var(--orange)}
.newsletter p{position:absolute;left:7px;top:29px;font-size:8px;color:var(--ink-soft)}
.field{position:absolute;left:7px;width:153px;height:16px;border:1px solid #e3e3e3;font-size:7px;color:#888;padding-left:6px;display:flex;align-items:center}
.btn-sub{position:absolute;left:8px;top:95px;width:63px;height:16px;background:var(--coral);border-radius:3px;color:var(--white);font-family:"Lobster",cursive;font-size:10px;display:flex;align-items:center;justify-content:center}

/* products */
.feat-rule{left:296px;top:617px;width:447px;height:1px;background:var(--line)}
.pager{top:592px;width:18px;height:16px;background:#7d7d7d;border-radius:2px}
.card{width:139px;height:150px;background:var(--white);box-shadow:0 0 4px rgba(0,0,0,.18)}
.card-img{position:absolute;left:12px;top:8px;width:115px;height:92px;border-bottom:1px solid var(--line)}
.card-name{position:absolute;left:0;top:108px;width:139px;text-align:center;font-family:"Lobster",cursive;font-size:9.5px;color:#555}
.card-link{position:absolute;left:0;top:128px;width:139px;text-align:center;font-size:8px;color:var(--orange);font-weight:600}

/* footer */
.footer{left:0;top:990px;width:835px;height:158px;background:var(--cream)}
.foot-h{top:1006px;font-family:"Lobster",cursive;font-size:14px;color:#666}
.foot-rule{top:1031px;height:1px;background:#e8e2dc}
.foot-txt{font-size:8px;line-height:13.5px;color:#777}
.orange{color:var(--orange)}
.social{left:645px;display:flex;align-items:center;gap:8px;font-size:8px;color:#555}
.social i{display:block;width:19px;height:19px;border-radius:50%}
.bottom-bar{left:0;top:1148px;width:835px;height:52px;background:var(--dark);color:var(--white);font-size:8px;display:flex;align-items:center;justify-content:center;gap:5px}
</style>
</head>
<body>

<header class="abs site-header"></header>
<div class="abs brand"><span class="brand-name">The Velvet Lantern</span></div>
<nav class="abs nav">
  <a class="current" href="#">Home</a><a href="#">About</a><a href="#">Online Store</a><a href="#">Blog</a><a href="#">Contact us</a>
</nav>

<section class="abs hero" role="img" aria-label="Soft peach banner with a hanging crystal pendant and a woman wearing gold jewellery"></section>
<div class="abs hero-photo"></div>
<h1 class="abs hero-title script" style="font-weight:400">Neque quisquam</h1>
<p class="abs hero-text">Est qui dolorem ipsumNeque porrpsumNeq quisquam est qui dolorem ipsumm</p>
<div class="abs hero-btn">View More</div>
<svg class="abs hero-arrow" style="left:7px" width="42" height="42" viewBox="0 0 42 42"><circle cx="21" cy="21" r="19" fill="none" stroke="#fff" stroke-width="2.5"/><path d="M25 11 L14 21 L25 31" fill="none" stroke="#fff" stroke-width="4"/></svg>
<svg class="abs hero-arrow" style="left:779px" width="42" height="42" viewBox="0 0 42 42"><circle cx="21" cy="21" r="19" fill="none" stroke="#fff" stroke-width="2.5"/><path d="M17 11 L28 21 L17 31" fill="none" stroke="#fff" stroke-width="4"/></svg>

<section class="abs promos"></section>
<div class="abs promo" style="left:91px;background:linear-gradient(115deg,#f6c189 0%,#f8cfa1 55%,#9a6a4a 75%,#d9a57c 100%)" role="img" aria-label="Stack of old books">
  <div class="abs promo-label script" style="color:#fff">New<br>Collections</div>
  <div class="abs promo-link" style="color:#fff">View Here ▸</div>
</div>
<div class="abs promo" style="left:316px;background:linear-gradient(115deg,#f7c896 0%,#f9d6ae 50%,#c99063 72%,#7b93a8 100%)" role="img" aria-label="Wooden pendulums laid in a row">
  <div class="abs promo-label script" style="color:var(--coral-dark)">Best<br>Sellers</div>
  <div class="abs promo-rule" style="background:var(--coral-dark)"></div>
  <div class="abs promo-link" style="color:var(--coral-dark)">View Here ▸</div>
</div>
<div class="abs promo" style="left:540px;background:linear-gradient(115deg,#f8d3a5 0%,#fbe1bf 50%,#e9b852 75%,#f0c767 100%)" role="img" aria-label="Golden wrapped gift boxes">
  <div class="abs promo-label script" style="color:#444">Get<br>More Gifts</div>
  <div class="abs promo-rule" style="background:#444"></div>
  <div class="abs promo-link" style="color:#333">View Here ▸</div>
</div>

<h2 class="abs section-title" style="left:91px;top:588px;font-weight:400">Shop By Categories</h2>
<ul class="abs cat-list">
  <li>Crystals</li><li>Books</li><li>CD's</li><li>Pendulums</li><li>Metaphysical items</li><li>Reiki (energy healing)</li><li>Other Products</li>
</ul>

<div class="abs newsletter">
  <h3>Subscribe Newsletter</h3>
  <p>Sign up for our newsletter</p>
  <div class="field" style="top:46px">Name:</div>
  <div class="field" style="top:68px">Email:</div>
  <div class="btn-sub">Subscribe</div>
</div>

<h2 class="abs section-title" style="left:296px;top:588px;font-weight:400">Featured products</h2>
<div class="abs feat-rule"></div>
<svg class="abs pager" style="left:703px" width="18" height="16" viewBox="0 0 18 16"><path d="M10.5 4.5 L7 8 L10.5 11.5" fill="none" stroke="#fff" stroke-width="1.5"/></svg>
<svg class="abs pager" style="left:725px" width="18" height="16" viewBox="0 0 18 16"><path d="M7.5 4.5 L11 8 L7.5 11.5" fill="none" stroke="#fff" stroke-width="1.5"/></svg>

<div class="abs card" style="left:297px;top:632px"><div class="card-img" role="img" aria-label="Purple and green crystals" style="background:radial-gradient(circle at 40% 50%,#b79bd8 0,#d9c8ec 40%,#fff 70%)"></div><div class="card-name">Crystalsi Long Sleeved</div><div class="card-link">▸ View Details</div></div>
<div class="abs card" style="left:450px;top:632px"><div class="card-img" role="img" aria-label="Stack of coloured books" style="background:radial-gradient(circle at 50% 50%,#c0454f 0,#e8b4b8 35%,#fff 68%)"></div><div class="card-name">Books Long Sleeved</div><div class="card-link">▸ View Details</div></div>
<div class="abs card" style="left:604px;top:632px"><div class="card-img" role="img" aria-label="Stack of compact discs" style="background:radial-gradient(circle at 50% 50%,#c9d6cf 0,#7fa79a 30%,#e6eeea 50%,#fff 68%)"></div><div class="card-name">CDs Long Sleeved</div><div class="card-link">▸ View Details</div></div>
<div class="abs card" style="left:297px;top:802px"><div class="card-img" role="img" aria-label="Hanging crystal pendulums" style="background:radial-gradient(circle at 50% 60%,#d9c1c1 0,#efe3e3 35%,#fff 65%)"></div><div class="card-name">Pendulums Long Sleeved</div><div class="card-link">▸ View Details</div></div>
<div class="abs card" style="left:450px;top:802px"><div class="card-img" role="img" aria-label="Aqua crystal block" style="background:radial-gradient(circle at 50% 55%,#4fb6c4 0,#9ddbe2 38%,#fff 68%)"></div><div class="card-name">Metaphysical Long Sleeved</div><div class="card-link">▸ View Details</div></div>
<div class="abs card" style="left:604px;top:802px"><div class="card-img" role="img" aria-label="Healing stones in a white dish" style="background:radial-gradient(circle at 45% 50%,#8c98a0 0,#c7b2a8 35%,#f2eeee 55%,#fff 70%)"></div><div class="card-name">Energy healing Long Sle</div><div class="card-link">▸ View Details</div></div>

<footer class="abs footer"></footer>
<h3 class="abs foot-h" style="left:91px;font-weight:400">About Us</h3>
<div class="abs foot-rule" style="left:91px;width:148px"></div>
<p class="abs foot-txt" style="left:91px;top:1042px;width:150px">Lorem ipsum dolor sit amet, consecte adipisicing elit, sed do eiusmod tebm incididunt ut labore et dolore magn liqua. Ut enim ad mini<br><span class="orange">Read More</span></p>

<h3 class="abs foot-h" style="left:276px;font-weight:400">Contact Us</h3>
<div class="abs foot-rule" style="left:276px;width:148px"></div>
<div class="abs foot-txt" style="left:276px;top:1043px">Address:</div>
<div class="abs foot-txt" style="left:326px;top:1043px;width:110px">48 Willow Row, Amber Court 12, Fernvale</div>
<div class="abs foot-txt" style="left:276px;top:1091px">Phone:</div>
<div class="abs foot-txt" style="left:326px;top:1091px;color:#555">+1 555 014 2290</div>
<div class="abs foot-txt" style="left:276px;top:1111px">Email:</div>
<div class="abs foot-txt orange" style="left:326px;top:1111px;font-size:9px">hello@velvetlantern.com</div>

<h3 class="abs foot-h" style="left:472px;font-weight:400">Latest Tweets</h3>
<div class="abs foot-rule" style="left:472px;width:124px"></div>
<div class="abs foot-txt" style="left:472px;top:1044px;display:flex;gap:8px;align-items:center"><svg width="12" height="10" viewBox="0 0 12 10"><circle cx="6" cy="5" r="4.5" fill="#666"/></svg><span class="orange" style="font-size:7.5px">rganisation working towards</span></div>
<p class="abs foot-txt" style="left:473px;top:1064px;width:140px">Experience the most luxurious and enjoyable pet resort in the Fox Valley, dedicated to the .</p>
<div class="abs foot-txt orange" style="left:473px;top:1110px;font-size:9px">hello@velvetlantern.com</div>

<h3 class="abs foot-h" style="left:645px;font-weight:400">Follow Us</h3>
<div class="abs foot-rule" style="left:645px;width:98px"></div>
<div class="abs social" style="top:1044px"><i style="background:#29b6e8"></i>Chirpline</div>
<div class="abs social" style="top:1076px"><i style="background:#3b6cc4"></i>Friendwall</div>
<div class="abs social" style="top:1108px"><i style="background:#e5261f"></i>Circles</div>

<div class="abs bottom-bar">Copyright © 2014 All Rights Reserved. <span class="orange">About Us</span><span class="orange">|</span><span class="orange">Privacy Policy</span></div>

</body>
</html>
```